Business Card Design for Training Business

Clear Path Coaching is a new business that delivers training and other services with a focus on topics related to mental health and wellbeing, for example, Wellmind Response Course, Resilience etc. We have a strong focus on evidence-based psychology and neuroscience. I have a logo which I will upload with the brief, so please consider colours that work well with the logo.
Target Market(s)
Adults, workplaces (particularly government and not-for-profits)
Industry/Entity Type
Business
Contact Information for Business Card
Head Strong TrainingSamantha SellwoodDirector0438 770 850sam@headstrongtraining.com.auwww.headstrongtraining.com.au

```html
<!DOCTYPE html>
<html lang="en">
<head>
<meta charset="utf-8">
<title>Clear Path Coaching – Business Card</title>
<link rel="stylesheet" href="https://fonts.googleapis.com/css2?family=Cormorant+Garamond:ital,wght@1,600&family=Open+Sans:wght@300;400&display=swap">
<style>
  :root {
    --teal: #138f91;
    --teal-dark: #0f7f82;
    --teal-soft: #7fd0d2;
    --ink: #2f2f2f;
    --grey: #4a4a4a;
    --paper: #ffffff;
    --backdrop: #e9ecec;
  }
  * { box-sizing: border-box; margin: 0; padding: 0; }
  html, body { width: 1200px; height: 892px; overflow: hidden; background: var(--backdrop); }
  .card {
    position: absolute; left: 40px; top: 104px;
    width: 1120px; height: 684px;
    background: var(--paper);
    box-shadow: 0 10px 30px rgba(0,0,0,.12);
    overflow: hidden;
  }
  .card__band { position: absolute; inset: 0; }
  .brand {
    position: absolute; right: 112px; top: 128px;
    display: flex; flex-direction: column; align-items: flex-end; gap: 18px;
  }
  .brand__dot {
    width: 124px; height: 124px; border-radius: 50%;
    background: var(--teal-soft); margin-right: 80px;
  }
  .brand__name {
    font-family: "Open Sans", sans-serif; font-weight: 300;
    font-size: 40px; letter-spacing: 5px; text-transform: uppercase;
    color: var(--ink);
  }
  .person {
    position: absolute; right: 112px; top: 372px; text-align: right;
  }
  .person__name {
    font-family: "Cormorant Garamond", serif; font-style: italic; font-weight: 600;
    font-size: 56px; color: var(--teal); letter-spacing: 1px; line-height: 1.05;
  }
  .person__role {
    font-family: "Open Sans", sans-serif; font-size: 26px; color: var(--ink);
  }
  .contact {
    position: absolute; right: 84px; top: 498px;
    list-style: none; display: flex; flex-direction: column; gap: 10px;
    font-family: "Open Sans", sans-serif; font-size: 26px; color: var(--ink);
  }
  .contact__item { display: flex; align-items: center; justify-content: flex-end; gap: 18px; }
  .contact__icon { width: 30px; height: 30px; flex: none; }
</style>
</head>
<body>
  <article class="card">
    <svg class="card__band" width="1120" height="684" viewBox="0 0 1120 684" aria-hidden="true">
      <polygon points="370,0 526,0 318,684 124,684" fill="var(--teal)"/>
      <polygon points="370,0 526,0 470,184 330,184" fill="var(--teal-dark)"/>
      <circle cx="336" cy="253" r="150" fill="var(--teal)"/>
      <circle cx="336" cy="253" r="136" fill="var(--paper)"/>
    </svg>

    <div class="brand">
      <span class="brand__dot"></span>
      <span class="brand__name">Clear Path Coaching</span>
    </div>

    <div class="person">
      <p class="person__name">Rebecca Tanfield</p>
      <p class="person__role">Director</p>
    </div>

    <ul class="contact">
      <li class="contact__item">
        <span>0491 362 517</span>
        <svg class="contact__icon" viewBox="0 0 30 30" aria-label="Phone">
          <rect width="30" height="30" rx="4" fill="var(--ink)"/>
          <path d="M10 7 l4 0 l1 5 l-3 2 q2 4 5 5 l2 -3 l5 1 l0 4 q-1 2 -4 2 q-11 -2 -12 -13 q0 -3 2 -3z" fill="#fff"/>
        </svg>
      </li>
      <li class="contact__item">
        <span>bec@clearpathcoaching.example.au</span>
        <svg class="contact__icon" viewBox="0 0 30 30" aria-label="Email">
          <rect width="30" height="30" rx="4" fill="var(--ink)"/>
          <rect x="6" y="9" width="18" height="12" fill="none" stroke="#fff" stroke-width="2"/>
          <path d="M6 9 l9 7 l9 -7" fill="none" stroke="#fff" stroke-width="2"/>
        </svg>
      </li>
      <li class="contact__item">
        <span>www.clearpathcoaching.example.au</span>
        <svg class="contact__icon" viewBox="0 0 30 30" aria-label="Website">
          <rect width="30" height="30" rx="4" fill="var(--ink)"/>
          <circle cx="15" cy="15" r="8" fill="none" stroke="#fff" stroke-width="2"/>
          <ellipse cx="15" cy="15" rx="3.5" ry="8" fill="none" stroke="#fff" stroke-width="1.5"/>
          <line x1="7" y1="15" x2="23" y2="15" stroke="#fff" stroke-width="1.5"/>
        </svg>
      </li>
    </ul>
  </article>
</body>
</html>
```